Coastal Gin Label Design

We are needing a nautical/coastal themed label for our upcoming gin release.

We have saltbush, cucumber, juniper, and quandong being used in this gin.

Name of the Gin; Harbour Moons

The logo attached is the company logo, but doesn't have to be used on the front of the label, ie it can just be the name Fernwhistle somewhere on the front.
Bottle specs attached as well so you can accurately represent the bottle- this bottle is also clear.

Target Market(s)

Women 25- 45

Font styles to use
Serif
Decorative

Colors
d5edf4
86cae7
33a6d7
86cfc6
cfeae6
ffffff
f6faec
ecf7fb
fefeff

Requirements
Must have
• Ocean/Coastal vibe to the label
Nice to have
• Blues,Whites clean and crisp
Should not have
• No generic word art look to it.
A dark mood

```html
<!DOCTYPE html>
<html lang="en">
<head>
<meta charset="utf-8">
<title>Harbour Moons – Gin Label</title>
<link rel="stylesheet" href="https://fonts.googleapis.com/css2?family=Cinzel:wght@600;700&family=Josefin+Sans:wght@400;600&family=Oswald:wght@300;500&display=swap">
<style>
  :root {
    --ink-blue: #1d4b9b;
    --deep-band: #1f4f9e;
    --sky-top: #a9cdeb;
    --sky-mid: #d5edf4;
    --haze: #ecf7fb;
    --sea-light: #86cae7;
    --sea-mid: #33a6d7;
    --sea-teal: #86cfc6;
    --paper: #fefeff;
    --text-grey: #3d4450;
    --accent-blue: #2f6fc4;
    --warn-red: #e0242b;
    --icon-fill: #9ec8dc;
    --page: #ffffff;
  }
  * { box-sizing: border-box; margin: 0; padding: 0; }
  html, body { width: 1079px; height: 1200px; overflow: hidden; background: var(--page); }
  .canvas { position: relative; width: 1079px; height: 1200px; }

  .label {
    position: absolute; top: 70px; width: 510px; height: 552px; overflow: hidden;
  }
  .label--front { left: 20px; }
  .label--back { left: 549px; }

  .scene-photo {
    position: absolute; inset: 0;
    background: linear-gradient(180deg, var(--sky-top) 0%, var(--sky-mid) 20%, var(--haze) 42%, #e6f2f6 56%, var(--sea-light) 58%, var(--sea-mid) 72%, var(--sea-teal) 86%, #6fb8c9 92%);
  }

  .brand-line {
    position: absolute; top: 40px; width: 100%; text-align: center;
    font-family: "Josefin Sans", sans-serif; font-weight: 400; font-size: 17px;
    letter-spacing: 0.2em; color: var(--ink-blue); text-transform: uppercase;
  }
  .front-title {
    position: absolute; top: 72px; width: 100%; text-align: center;
    font-family: "Cinzel", serif; font-weight: 700; color: var(--ink-blue);
    font-size: 70px; line-height: 82px; letter-spacing: 0.01em;
    text-shadow: 0 1px 0 #ffffff;
  }

  .spec-band {
    position: absolute; left: 0; right: 0; top: 496px; height: 50px;
    background: var(--deep-band); color: #ffffff;
    display: flex; align-items: center; justify-content: center;
    font-family: "Josefin Sans", sans-serif; font-weight: 600; font-size: 14px; letter-spacing: 0.12em;
  }
  .spec-band::before {
    content: ""; position: absolute; left: 0; right: 0; top: -4px; height: 4px;
    background: repeating-linear-gradient(90deg, var(--deep-band) 0 3px, transparent 3px 5px);
  }

  .back-panel {
    position: absolute; left: 0; right: 0; top: 0; height: 309px;
    background: linear-gradient(180deg, var(--sky-mid) 0%, var(--haze) 25%, var(--paper) 60%, var(--haze) 100%);
  }
  .back-title {
    position: absolute; top: 44px; width: 100%; text-align: center;
    font-family: "Cinzel", serif; font-weight: 700; font-size: 36px; color: var(--ink-blue);
  }
  .back-story {
    position: absolute; left: 100px; width: 310px; top: 100px;
    font-family: "Oswald", sans-serif; font-weight: 300; font-size: 12px; line-height: 17px;
    color: var(--text-grey); text-align: justify; text-align-last: center;
  }
  .ingredients {
    position: absolute; left: 100px; top: 244px;
    font-family: "Oswald", sans-serif; font-weight: 500; font-size: 10.5px; line-height: 17px; color: #1e2430;
  }
  .ingredients__head { color: var(--accent-blue); }
  .maker-mark {
    position: absolute; right: 100px; top: 262px;
    display: flex; align-items: center; gap: 6px;
    font-family: "Cinzel", serif; font-weight: 600; font-size: 17px; color: var(--text-grey);
  }
  .maker-mark__dot { width: 10px; height: 10px; border-radius: 50%; background: var(--text-grey); }

  .warnings {
    position: absolute; top: 347px; left: 0; right: 0;
    display: flex; justify-content: center; align-items: center; gap: 18px;
  }
  .warnings__divider { width: 1px; height: 34px; background: rgba(255,255,255,0.7); }

  .neck-strip {
    position: absolute; top: 680px; width: 66px; height: 250px; background: var(--paper);
    border: 1px solid #e2edf2;
    display: flex; align-items: center; justify-content: center;
  }
  .neck-strip--front { left: 242px; }
  .neck-strip--back { left: 771px; }
  .neck-strip span {
    writing-mode: vertical-rl; transform: rotate(180deg);
    font-family: "Cinzel", serif; font-weight: 700; font-size: 22px; color: var(--ink-blue); letter-spacing: 0.02em;
  }
</style>
</head>
<body>
<main class="canvas">

  <section class="label label--front">
    <div class="scene-photo" role="img" aria-label="Photograph of a small wooded island on the horizon under a pale blue sky, with a clear turquoise sea and rocks in the foreground"></div>
    <p class="brand-line">Fernwhistle</p>
    <h1 class="front-title">HARBOUR<br>MOONS</h1>
    <div class="spec-band">700 ML. &nbsp;|&nbsp; 43% ALC. VOL.&nbsp;| &nbsp;SMALL BATCH</div>
  </section>

  <section class="label label--back">
    <div class="scene-photo" role="img" aria-label="Photograph of a clear turquoise sea with rocks in the foreground"></div>
    <div class="back-panel"></div>
    <h2 class="back-title">HARBOUR MOONS</h2>
    <p class="back-story">Lorem Ipsum is simply dummy text of the printing and typesetting industry. Lorem Ipsum has been the industry's standard dummy text ever since the 1500s, when an unknown printer took a galley of type and scrambled it to make a type specimen book. It has survived not only five centuries, but also the leap into electronic typesetting, remaining essentially unchanged. It was popularised. Lorem Ipsum is simply dummy text of the printing and typesetting industry.</p>
    <div class="ingredients">
      <div class="ingredients__head">INGREDIENTS:</div>
      <div>SALTBUSH, CUCUMBER,</div>
      <div>JUNIPER, AND QUANDONG</div>
    </div>
    <div class="maker-mark"><span class="maker-mark__dot"></span>FERNWHISTLE</div>

    <div class="warnings">
      <svg class="warning warning--driving" width="44" height="44" viewBox="0 0 44 44" aria-label="Do not drink and drive">
        <circle cx="22" cy="22" r="19" fill="var(--icon-fill)" stroke="var(--warn-red)" stroke-width="3.5"/>
        <rect x="12" y="20" width="20" height="9" rx="3" fill="#ffffff"/>
        <path d="M15 20 L18 14 H26 L29 20 Z" fill="#ffffff"/>
        <line x1="9" y1="9" x2="35" y2="35" stroke="var(--warn-red)" stroke-width="3.5"/>
      </svg>
      <span class="warnings__divider"></span>
      <svg class="warning warning--pregnancy" width="44" height="44" viewBox="0 0 44 44" aria-label="Not for pregnant women">
        <circle cx="22" cy="22" r="19" fill="var(--icon-fill)" stroke="var(--warn-red)" stroke-width="3.5"/>
        <circle cx="20" cy="12" r="3" fill="#ffffff"/>
        <path d="M18 16 H23 C28 20 28 27 23 29 L22 34 H19 L18 29 Z" fill="#ffffff"/>
        <line x1="9" y1="9" x2="35" y2="35" stroke="var(--warn-red)" stroke-width="3.5"/>
      </svg>
      <span class="warnings__divider"></span>
      <svg class="warning warning--age" width="44" height="44" viewBox="0 0 44 44" aria-label="Not for under 18">
        <circle cx="22" cy="22" r="19" fill="var(--icon-fill)" stroke="var(--warn-red)" stroke-width="3.5"/>
        <text x="22" y="27" text-anchor="middle" font-family="Oswald, sans-serif" font-weight="500" font-size="15" fill="#ffffff">18+</text>
        <line x1="9" y1="9" x2="35" y2="35" stroke="var(--warn-red)" stroke-width="3.5"/>
      </svg>
    </div>

    <div class="spec-band">700 ML. &nbsp;|&nbsp; 43% ALC. VOL.&nbsp;| &nbsp;SMALL BATCH</div>
  </section>

  <div class="neck-strip neck-strip--front"><span>HARBOUR MOONS</span></div>
  <div class="neck-strip neck-strip--back"><span>HARBOUR MOONS</span></div>

</main>
</body>
</html>
```